Public Relations Agency Seeks Wordpress Design and Coding

TRELVOX Studio is a public relations agency specializing in media relations, public affairs and marketing communication.

The site should display the following visual characteristics: professionalism, trustworthiness, high-tech focus, clear and concise design.

The desired colors are royal blue, gray and hints of red.

Design look/feel inspired by this site: http://brightpathgatherings.example/

Specifications:

1. Navigation/Pages/Index:

HOME

ABOUT US

SERVICES

NEWS

CONTACT

---

2. Functionality of/content for each page:

- Home
o Dominant photo (professional, edgy, innovative)
o Simple, straightforward access to/from “Home” from other pages
o Includes logo (attached) and tagline "Unleash the power of communication"
o Direct link to “CONTACT”
o Links to social media accounts: Facebook, Twitter, LinkedIn

- About Us

o Company profile blurb
o President’s photo with short bio

- Services
o Public Relations
 Strategic communication
 Brand and reputation management
 Community relations
o Media Relations
 News coverage and contacts
 Media training and interview skills
 Crisis communications
o Congressional Affairs
 Public affairs
 Public policy
 Legislative strategy
o Mass Communication
 Speechwriting
 Presentation creation
 Social media
o Marketing Communications
 Business collateral material
 Promotional campaigns
 Special events and tradeshows

- News
o Blog-like page to post information and/or share news from other sites

- Contact
o Standard “Contact Us” form (Name, Email, Phone, Message)
o Direct Contact
 (407) 555-0164
 Marisol@TRELVOXstudio.example

Target Market(s)

Small to large businesses specializing in high technology, defense/military, medicine/healthcare, and wide array of professional services.

Industry/Entity Type

Marketing

Font styles to use
Serif
Sans Serif

Colors
0555a3
ec2027
edf3f7

Requirements
Must have
• -- Project reqires DESIGN - and - fully CODED.

-- Strong SEO

-- Optimized for mobile viewing

Thank you!

```html
<!DOCTYPE html>
<html lang="en">
<head>
<meta charset="utf-8">
<title>TRELVOX Studio — Public Relations Agency</title>
<link rel="stylesheet" href="https://fonts.googleapis.com/css2?family=Open+Sans:wght@300;400;600;700;800&display=swap">
<style>
:root{
  --blue:#1f3c96;
  --red:#c52a1e;
  --grey-text:#5c5c5c;
  --grey-light:#e3e3e3;
  --white:#ffffff;
  --hero-a:#3b3a3f;
  --hero-b:#6f6a66;
  --about-a:#3a3631;
  --about-b:#6b5a44;
}
*{box-sizing:border-box;margin:0;padding:0}
html,body{width:1200px;height:3051px;overflow:hidden}
body{position:relative;background:var(--white);font-family:"Open Sans",Arial,sans-serif;color:var(--grey-text)}
.abs{position:absolute}

/* Hero */
.hero{left:0;top:0;width:1200px;height:746px;background:radial-gradient(ellipse at 50% 45%,var(--hero-b),var(--hero-a) 75%)}
.hero-brand{left:0;width:1200px;top:224px;text-align:center;font-weight:700;font-size:32px;letter-spacing:2px;color:#1a1a1a}
.hero-title{left:0;width:1200px;top:289px;text-align:center;font-weight:800;font-size:57px;line-height:72px;color:var(--white);letter-spacing:1px}
.hero-call{left:0;width:1200px;top:527px;text-align:center;font-size:23px;color:var(--white)}
.hero-call span{margin-left:14px}
.search-btn{left:1007px;top:55px;width:92px;height:93px;background:var(--blue)}
.slider-dots{left:562px;top:711px;display:flex;gap:6px}
.slider-dots i{display:block;width:13px;height:13px;border-radius:50%;background:var(--white)}
.slider-dots i.active{background:var(--red)}

/* Header */
.site-header{left:0;top:746px;width:1200px;height:109px;background:var(--white);box-shadow:0 3px 4px rgba(0,0,0,.12)}
.header-brand{left:102px;top:28px;font-weight:700;font-size:32px;color:#555;letter-spacing:1px;line-height:52px}
.main-nav{right:102px;top:44px;display:flex;gap:35px;font-size:15px;text-transform:uppercase;color:#444}
.main-nav .current{color:var(--blue)}

/* Section headings */
.section-title{left:0;width:1200px;text-align:center;font-weight:400;font-size:37px;color:#555}
.section-title em{font-style:normal;color:var(--red)}

/* What we do */
.intro{left:100px;width:1000px;top:986px;text-align:center;font-size:14.4px;line-height:21px;color:#555}
.service{width:260px;text-align:center;font-size:24px;line-height:29px;color:#6d6d6d}
.service.active{color:var(--red)}
.service-icon{width:118px;height:118px;margin:0 auto 16px;display:flex;align-items:center;justify-content:center}
.service.active .service-icon{background:var(--red);border-radius:50%}

/* About */
.about{left:0;top:1389px;width:1200px;height:466px;background:linear-gradient(100deg,var(--about-a),var(--about-b) 55%,#4a4036)}
.president-photo{left:102px;top:1515px;width:224px;height:273px;border:2px solid #bbb;background:linear-gradient(160deg,#9a8f8a,#b44a3c 70%,#8a2a22)}
.about-text{left:362px;top:1513px;width:738px;font-size:16px;line-height:23px;color:var(--white)}
.btn-read{left:932px;top:1745px;width:166px;height:39px;background:var(--blue);color:var(--white);font-size:15px;line-height:39px;text-align:center}

/* News */
.news-card{top:1989px;width:317px}
.news-image{width:100%;height:218px}
.news-title{margin-top:26px;font-size:18px;font-weight:400;letter-spacing:.8px;color:#333}
.news-card.featured .news-title{color:var(--blue)}
.news-excerpt{margin-top:22px;width:272px;font-size:12.5px;line-height:23px;color:#777;letter-spacing:.3px}
.news-meta{margin-top:22px;display:flex;align-items:center;gap:10px;font-size:11px;color:#666}
.news-meta svg{flex:none}
.news-meta .gap{width:30px}
.news-rule{left:443px;top:2463px;width:318px;height:4px;background:var(--blue)}
.divider{left:0;top:2553px;width:1200px;height:2px;background:#e0e0e0}

/* Contact */
.field{background:var(--grey-light);font-size:13px;color:#666;padding:8px 10px;text-transform:uppercase}
.field.message{text-transform:none;padding-top:12px}
.btn-send{left:488px;top:2860px;width:228px;height:28px;border-radius:4px;background:var(--red);color:var(--white);font-size:13.5px;line-height:28px;text-align:center;text-transform:uppercase;letter-spacing:.5px}

/* Footer */
.site-footer{left:0;top:2917px;width:1200px;height:134px;background:var(--blue)}
.footer-links{left:0;width:1200px;top:38px;text-align:center;font-size:13px;color:var(--white)}
.footer-links span{margin:0 8px}
.social{left:560px;top:80px;display:flex;gap:18px}
.social i{display:block;width:16px;height:16px;border-radius:50%;background:var(--white)}
</style>
</head>
<body>

<section class="hero abs" role="img" aria-label="Photo of a team stacking hands together in a circle, seen from below"></section>
<div class="hero-brand abs">TRELVOX Studio</div>
<h1 class="hero-title abs">UNLEASH THE<br>POWER OF<br>COMMUNICATION</h1>
<p class="hero-call abs">CALL US <span>1.800.555.0199</span></p>
<div class="search-btn abs">
  <svg width="92" height="93" viewBox="0 0 92 93"><circle cx="43" cy="43" r="12" fill="none" stroke="#fff" stroke-width="4"/><line x1="52" y1="52" x2="62" y2="62" stroke="#fff" stroke-width="5" stroke-linecap="round"/></svg>
</div>
<div class="slider-dots abs"><i class="active"></i><i></i><i></i><i></i></div>

<header class="site-header abs">
  <div class="header-brand abs">TRELVOX Studio</div>
  <nav class="main-nav abs">
    <span class="current">Home</span><span>About Us</span><span>Services</span><span>News</span><span>Contact Us</span>
  </nav>
</header>

<h2 class="section-title abs" style="top:910px">WHAT <em>WE</em> DO</h2>
<p class="intro abs">We are public relations agency specializing in media relations, public affairs and marketing communication. Lorem ipsum dolor sit amet, consectetur adipiscing elit. Nam id suscipit sapien. Cras hendrerit felis eu nibh lacinia, et malesuada quam tempus. Ut facilisis vehicula pulvinar. Donec tempor mattis cursus. Ut sodales nibh et feugiat cursus. Vivamus congue quis augue quis suscipit. In ornare cursus lorem sed venenatis. Duis sit amet dictum justo. Donec vitae lectus fermentum, feugiat arcu at, tincidunt metus. Suspendisse viverra ultricies nisl ac bibendum. Sed vestibulum ipsum non convallis gravida.</p>

<div class="service abs" style="left:198px;top:1121px">
  <div class="service-icon"><svg width="50" height="40" viewBox="0 0 50 40"><circle cx="30" cy="20" r="15" fill="none" stroke="#8a8a8a" stroke-width="4"/><circle cx="30" cy="20" r="6" fill="#8a8a8a"/><path d="M4 12 L18 20 L4 28 Z" fill="#8a8a8a"/></svg></div>
  Media Relations
</div>
<div class="service active abs" style="left:470px;top:1121px">
  <div class="service-icon"><svg width="60" height="40" viewBox="0 0 60 40"><g fill="#fff"><circle cx="18" cy="10" r="5"/><circle cx="42" cy="10" r="5"/><circle cx="30" cy="14" r="5"/><path d="M10 28 q8-12 16 0z"/><path d="M34 28 q8-12 16 0z"/><path d="M22 30 q8-12 16 0z"/><rect x="6" y="30" width="48" height="3"/></g></svg></div>
  Public Affairs
</div>
<div class="service abs" style="left:738px;top:1121px">
  <div class="service-icon"><svg width="56" height="40" viewBox="0 0 56 40"><path d="M6 14 h12 l22 -10 v32 l-22 -10 h-12 z" fill="#8a8a8a"/><rect x="12" y="26" width="7" height="10" fill="#8a8a8a"/><line x1="46" y1="20" x2="52" y2="20" stroke="#8a8a8a" stroke-width="3"/></svg></div>
  Marketing<br>Communication
</div>

<section class="about abs" role="img" aria-label="Blurred photo of a field at sunset"></section>
<h2 class="section-title abs" style="top:1420px;color:#fff">ABOUT <em>US</em></h2>
<div class="president-photo abs" role="img" aria-label="Portrait of the agency president in a red jacket beside a flag"></div>
<p class="about-text abs">In nec mattis felis. Curabitur nisl elit, euismod sit amet enim et, fermentum dictum felis. Nullam at ipsum vel nibh congue pulvinar. Mauris non sem vel nibh dapibus dapibus. Ut est dolor, blandit non tellus a, condimentum iaculis tellus. Praesent feugiat purus condimentum odio pellentesque, sit amet dignissim arcu pharetra. Ut dignissim mi iaculis purus iaculis rhoncus. Phasellus vel porta augue.<br>Nullam eget lectus ex. Sed porttitor congue ante. Aenean vitae nisl id libero auctor imperdiet. Donec tincidunt urna ut luctus laoreet. Donec pretium ipsum sed erat blandit finibus. Fusce quis leo sapien. Fusce sagittis nunc nisl, a luctus erat molestie scelerisque. Sed dignissim ut quam vel suscipit. Nulla scelerisque gravida suscipit.</p>
<div class="btn-read abs">Read More</div>

<h2 class="section-title abs" style="top:1910px">LATEST <em>NEWS</em></h2>

<article class="news-card abs" style="left:104px">
  <div class="news-image" role="img" aria-label="Illustration of connected people icons on a glowing blue network" style="background:linear-gradient(135deg,#0b3fa8,#2a7be0 55%,#0a2f86)"></div>
  <h3 class="news-title">Aliquam metus neque</h3>
  <p class="news-excerpt">bibendum sit amet porta at, consequat et enim. In ut turpis non ipsum rhoncus porttitor vel ac nunc. Maecenas interdum dignissim lorem quis auctor sit amet nulla nisl, aliquam pretium ipsum.</p>
  <div class="news-meta"><svg width="14" height="14" viewBox="0 0 14 14"><circle cx="7" cy="7" r="6" fill="none" stroke="#1f3c96" stroke-width="1.6"/><path d="M7 3.5V7h3" fill="none" stroke="#1f3c96" stroke-width="1.6"/></svg>September 02<span class="gap"></span><svg width="16" height="14" viewBox="0 0 16 14"><ellipse cx="8" cy="6" rx="7" ry="5" fill="#1f3c96"/><path d="M3 9 L2 13 L7 10z" fill="#1f3c96"/></svg>19</div>
</article>
<article class="news-card featured abs" style="left:445px">
  <div class="news-image" role="img" aria-label="Photo of a couple cheering on a sofa in a green field" style="background:linear-gradient(180deg,#b9c0a4,#8f9a6a 55%,#5b6a3a)"></div>
  <h3 class="news-title">Aliquam metus neque</h3>
  <p class="news-excerpt">bibendum sit amet porta at, consequat et enim. In ut turpis non ipsum rhoncus porttitor vel ac nunc. Maecenas interdum dignissim lorem quis auctor sit amet nulla nisl, aliquam pretium ipsum.</p>
  <div class="news-meta"><svg width="14" height="14" viewBox="0 0 14 14"><circle cx="7" cy="7" r="6" fill="none" stroke="#1f3c96" stroke-width="1.6"/><path d="M7 3.5V7h3" fill="none" stroke="#1f3c96" stroke-width="1.6"/></svg>September 02<span class="gap"></span><svg width="16" height="14" viewBox="0 0 16 14"><ellipse cx="8" cy="6" rx="7" ry="5" fill="#1f3c96"/><path d="M3 9 L2 13 L7 10z" fill="#1f3c96"/></svg>19</div>
</article>
<article class="news-card abs" style="left:791px;width:307px">
  <div class="news-image" role="img" aria-label="Photo of two business people reviewing a tablet at a desk" style="background:linear-gradient(135deg,#d9dde2,#8a98a8 50%,#3c4656)"></div>
  <h3 class="news-title">Aliquam metus neque</h3>
  <p class="news-excerpt">bibendum sit amet porta at, consequat et enim. In ut turpis non ipsum rhoncus porttitor vel ac nunc. Maecenas interdum dignissim lorem quis auctor sit amet nulla nisl, aliquam pretium ipsum.</p>
  <div class="news-meta"><svg width="14" height="14" viewBox="0 0 14 14"><circle cx="7" cy="7" r="6" fill="none" stroke="#1f3c96" stroke-width="1.6"/><path d="M7 3.5V7h3" fill="none" stroke="#1f3c96" stroke-width="1.6"/></svg>September 02<span class="gap"></span><svg width="16" height="14" viewBox="0 0 16 14"><ellipse cx="8" cy="6" rx="7" ry="5" fill="#1f3c96"/><path d="M3 9 L2 13 L7 10z" fill="#1f3c96"/></svg>19</div>
</article>
<div class="news-rule abs"></div>

<div class="divider abs"></div>

<h2 class="section-title abs" style="top:2582px">CONTACT <em>US</em></h2>
<div class="field abs" style="left:122px;top:2667px;width:299px;height:34px">Name</div>
<div class="field abs" style="left:454px;top:2667px;width:299px;height:34px">Phone Number</div>
<div class="field abs" style="left:783px;top:2667px;width:301px;height:34px">Email</div>
<div class="field message abs" style="left:122px;top:2728px;width:962px;height:83px">Type Your Message</div>
<div class="btn-send abs">Send the Message</div>

<footer class="site-footer abs">
  <p class="footer-links abs">Copyright © yourwebsite <span>|</span> Terms &amp; Conditions <span>|</span> Privacy Policy <span>|</span> Cookies Policy <span>|</span> Contact us</p>
  <div class="social abs" aria-label="Social profile links"><i aria-label="Social profile one"></i><i aria-label="Social profile two"></i><i aria-label="Social profile three"></i></div>
</footer>

</body>
</html>
```